Business Card Design for Training Business

Clear Path Coaching is a new business that delivers training and other services with a focus on topics related to mental health and wellbeing, for example, Wellmind Response Course, Resilience etc. We have a strong focus on evidence-based psychology and neuroscience. I have a logo which I will upload with the brief, so please consider colours that work well with the logo.
Target Market(s)
Adults, workplaces (particularly government and not-for-profits)
Industry/Entity Type
Business
Contact Information for Business Card
Head Strong TrainingSamantha SellwoodDirector0438 770 850sam@headstrongtraining.com.auwww.headstrongtraining.com.au

```html
<!DOCTYPE html>
<html lang="en">
<head>
<meta charset="utf-8">
<title>Clear Path Coaching – Business Card</title>
<link rel="stylesheet" href="https://fonts.googleapis.com/css2?family=Source+Sans+3:wght@400&display=swap">
<style>
  :root {
    --backdrop: #1e1f21;
    --card: #f3f3f1;
    --teal: #2f8f92;
    --brand-dot: #9fd3d3;
    --brand-text: #7d716c;
    --ink: #1d1d1d;
    --icon-bg: #1d1d1d;
    --icon-fg: #f3f3f1;
  }
  * { box-sizing: border-box; margin: 0; padding: 0; }
  html, body {
    width: 1200px;
    height: 1200px;
    overflow: hidden;
    background: var(--backdrop);
  }
  body {
    display: flex;
    align-items: center;
    justify-content: center;
    font-family: "Source Sans 3", sans-serif;
  }
  .card {
    width: 580px;
    height: 950px;
    background: var(--card);
    display: flex;
    flex-direction: column;
    align-items: center;
    padding-top: 90px;
    text-align: center;
  }
  .brand-dot {
    width: 150px;
    height: 150px;
    border-radius: 50%;
    background: var(--brand-dot);
  }
  .brand-name {
    margin-top: 40px;
    color: var(--brand-text);
    font-size: 44px;
    font-weight: 400;
    line-height: 1.1;
  }
  .person-name {
    margin-top: 56px;
    color: var(--teal);
    font-size: 42px;
    font-weight: 400;
  }
  .person-role {
    margin-top: 6px;
    color: var(--ink);
    font-size: 22px;
    font-weight: 400;
  }
  .contact-list {
    list-style: none;
    margin-top: 76px;
    display: flex;
    flex-direction: column;
    align-items: center;
    gap: 12px;
    color: var(--ink);
    font-size: 25px;
  }
  .contact-item {
    display: flex;
    flex-direction: column;
    align-items: center;
    gap: 6px;
  }
  .contact-icon {
    width: 26px;
    height: 26px;
    display: block;
  }
</style>
</head>
<body>
  <main class="card">
    <div class="brand-dot" aria-hidden="true"></div>
    <h1 class="brand-name">Clear Path Coaching</h1>
    <h2 class="person-name">Rebecca Tanfield</h2>
    <p class="person-role">Director</p>

    <ul class="contact-list">
      <li class="contact-item">
        <svg class="contact-icon" viewBox="0 0 26 26" aria-label="Phone">
          <rect width="26" height="26" rx="2" fill="var(--icon-bg)"/>
          <path d="M8 6 L11 6 L12 10 L10 11.5 Q12 15.5 15 17 L16.5 15 L20 16 L20 19 Q19 21 16 20 Q9 17 6.5 10 Q6 7 8 6 Z" fill="var(--icon-fg)"/>
        </svg>
        <span>0491 362 517</span>
      </li>
      <li class="contact-item">
        <svg class="contact-icon" viewBox="0 0 26 26" aria-label="Email">
          <rect width="26" height="26" rx="2" fill="var(--icon-bg)"/>
          <rect x="5" y="8" width="16" height="11" fill="none" stroke="var(--icon-fg)" stroke-width="1.6"/>
          <path d="M5 8 L13 14 L21 8" fill="none" stroke="var(--icon-fg)" stroke-width="1.6"/>
        </svg>
        <span>bec@clearpathcoaching.example.au</span>
      </li>
      <li class="contact-item">
        <svg class="contact-icon" viewBox="0 0 26 26" aria-label="Website">
          <rect width="26" height="26" rx="2" fill="var(--icon-bg)"/>
          <circle cx="13" cy="13" r="7.5" fill="none" stroke="var(--icon-fg)" stroke-width="1.5"/>
          <ellipse cx="13" cy="13" rx="3.2" ry="7.5" fill="none" stroke="var(--icon-fg)" stroke-width="1.3"/>
          <line x1="5.5" y1="13" x2="20.5" y2="13" stroke="var(--icon-fg)" stroke-width="1.3"/>
        </svg>
        <span>www.clearpathcoaching.example.au</span>
      </li>
    </ul>
  </main>
</body>
</html>
```